Business Card Design Project

I need a business card designed from scratch. I have an existing logo that I can upload in Illustrator for modification or redesign.

The Company is called Query Lanterns http://querylanterns.com.au and we provide Search Engine Optimization services to Australian businesses. The current logo signifies an increase in visitors, profits etc...

There are no restrictions as to the redesign - colours, style etc are all open to change.

Cards will be full colour and one sided printed at http://www.cardmoxel.com.au so check their requirements for file format and sizes etc.

I will expect all original files upon completion of project.

Target Market(s)

Any business with a web site looking to improve their search engine rankings

Industry/Entity Type

Business

Requirements
Must have
• I like modern, sleek designs. Clean, not fussy, uncluttered.

```html
<!DOCTYPE html>
<html lang="en">
<head>
<meta charset="utf-8">
<title>Query Lanterns — Business Card</title>
<link rel="stylesheet" href="https://fonts.googleapis.com/css2?family=Arimo:wght@400;700&display=swap">
<style>
  :root {
    --page: #ffffff;
    --brand-blue: #1f6db5;
    --navy-deep: #173866;
    --navy: #1e4f8f;
    --navy-bright: #2b6db3;
    --accent-yellow: #f6b51d;
    --accent-yellow-light: #f8d23a;
    --text-light: #ffffff;
  }
  * { box-sizing: border-box; margin: 0; padding: 0; }
  html, body {
    width: 1200px; height: 901px; overflow: hidden;
    background: var(--page);
    font-family: "Arimo", Arial, sans-serif;
  }
  .card {
    position: absolute; left: 109px; top: 164px;
    width: 996px; height: 560px;
    background: var(--page);
    box-shadow: 0 4px 10px rgba(0,0,0,0.28);
    overflow: hidden;
  }
  .brand {
    position: absolute; left: 86px; top: 62px;
    display: flex; align-items: center; gap: 40px;
  }
  .brand-dot {
    width: 120px; height: 120px; border-radius: 50%;
    background: var(--accent-yellow);
  }
  .brand-name {
    font-weight: 700; font-size: 74px; letter-spacing: -1px;
    color: var(--brand-blue);
  }
  .accent-band {
    position: absolute; left: 0; top: 282px; width: 100%; height: 13px;
    background: linear-gradient(90deg, var(--accent-yellow), var(--accent-yellow-light));
  }
  .info-panel {
    position: absolute; left: 0; top: 295px; width: 100%; height: 265px;
    background: radial-gradient(ellipse 420px 260px at 28% 55%, var(--navy-bright), transparent 75%),
                linear-gradient(90deg, var(--navy) 0%, var(--navy-deep) 80%);
    color: var(--text-light);
  }
  .pointer {
    position: absolute; left: 0; top: 36px;
    width: 0; height: 0;
    border-top: 30px solid transparent;
    border-bottom: 30px solid transparent;
    border-left: 33px solid var(--accent-yellow);
  }
  .person { position: absolute; left: 73px; top: 44px; }
  .person-name { font-weight: 700; font-size: 31px; line-height: 36px; }
  .person-title { font-size: 25px; line-height: 38px; color: var(--accent-yellow); }
  .address {
    position: absolute; left: 73px; top: 152px;
    font-size: 25px; line-height: 35px; font-style: normal;
  }
  .contacts {
    position: absolute; right: 52px; top: 46px;
    list-style: none;
  }
  .contacts li {
    display: flex; justify-content: flex-end; align-items: center; gap: 12px;
    font-size: 25px; line-height: 35px;
  }
  .contacts svg { width: 22px; height: 22px; fill: var(--accent-yellow); flex: none; }
</style>
</head>
<body>
  <main class="card">
    <div class="brand">
      <span class="brand-dot"></span>
      <span class="brand-name">Query Lanterns</span>
    </div>
    <div class="accent-band"></div>
    <section class="info-panel">
      <span class="pointer"></span>
      <div class="person">
        <p class="person-name">Marcus Ellery</p>
        <p class="person-title">Founder &amp; CEO</p>
      </div>
      <address class="address">1870 Willow Crest Rd #204<br>Tampa, FL 33602</address>
      <ul class="contacts">
        <li>1300 482 915
          <svg viewBox="0 0 24 24" aria-hidden="true"><path d="M6.6 10.8a15 15 0 0 0 6.6 6.6l2.2-2.2c.3-.3.7-.4 1-.2 1.1.4 2.3.6 3.6.6.6 0 1 .4 1 1V20c0 .6-.4 1-1 1A17 17 0 0 1 3 4c0-.6.4-1 1-1h3.5c.6 0 1 .4 1 1 0 1.3.2 2.5.6 3.6.1.3 0 .7-.2 1z"/></svg>
        </li>
        <li>1300 482 915
          <svg viewBox="0 0 24 24" aria-hidden="true"><path d="M7 1h10a2 2 0 0 1 2 2v18a2 2 0 0 1-2 2H7a2 2 0 0 1-2-2V3a2 2 0 0 1 2-2zm0 3v14h10V4zm5 15.5a1 1 0 1 0 0 2 1 1 0 0 0 0-2z"/></svg>
        </li>
        <li>1300 482 915
          <svg viewBox="0 0 24 24" aria-hidden="true"><path d="M6 2h12v5H6zM4 8h16a2 2 0 0 1 2 2v7h-4v5H6v-5H2v-7a2 2 0 0 1 2-2zm4 7v5h8v-5z"/></svg>
        </li>
        <li>enquiry@querylanterns.com.au
          <svg viewBox="0 0 24 24" aria-hidden="true"><path d="M2 5h20v14H2zm2 2v.5l8 5 8-5V7l-8 5z"/></svg>
        </li>
        <li>www.querylanterns.com.au
          <svg viewBox="0 0 24 24" aria-hidden="true"><path d="M12 2a10 10 0 1 0 0 20 10 10 0 0 0 0-20zm6.9 9h-3a15 15 0 0 0-1.3-5.9A8 8 0 0 1 18.9 11zM12 4c.9 1.2 1.8 3.7 1.9 7h-3.8c.1-3.3 1-5.8 1.9-7zM9.4 5.1A15 15 0 0 0 8.1 11h-3a8 8 0 0 1 4.3-5.9zM5.1 13h3a15 15 0 0 0 1.3 5.9A8 8 0 0 1 5.1 13zM12 20c-.9-1.2-1.8-3.7-1.9-7h3.8c-.1 3.3-1 5.8-1.9 7zm2.6-1.1a15 15 0 0 0 1.3-5.9h3a8 8 0 0 1-4.3 5.9z"/></svg>
        </li>
      </ul>
    </section>
  </main>
</body>
</html>
```